Using attached logo that has been created

Business card with logo that's attached. Maybe with water or the cartoon van in background. Looking for it to not be so plain and not too white.
Information to include;
Rodney Ashcombe
(555) 218-7730
Info@bramleypipeworks.example
www.bramleypipeworks.example
License # 4627195
Looking forward to the designs u come up with.
Thank you!
-Delphine
Target Market(s)
Plumbing
Industry/Entity Type
Plumbing
Contact Information for Business Card
Listed above

```html
<!DOCTYPE html>
<html lang="en">
<head>
<meta charset="UTF-8">
<title>Bramley Pipeworks – Business Card</title>
<link rel="stylesheet" href="https://fonts.googleapis.com/css2?family=Roboto:wght@400;500;700&display=swap">
<style>
  :root {
    --page-bg: #e4e4e4;
    --card-white: #ffffff;
    --brand-blue: #1559b7;
    --brand-yellow: #f2b200;
    --ink: #1e1e1e;
    --water-light: #5cc3e6;
    --water-mid: #2f9fcf;
    --water-deep: #17709c;
    --figure-blue: #2262c8;
    --figure-tan: #a88b62;
  }
  * { box-sizing: border-box; margin: 0; padding: 0; }
  html, body {
    width: 1200px; height: 800px; overflow: hidden;
    background: var(--page-bg);
    font-family: "Roboto", Arial, sans-serif;
  }
  .sheet {
    width: 1200px; height: 800px;
    display: flex; align-items: center; justify-content: center; gap: 40px;
  }
  .card {
    width: 560px; height: 320px; position: relative; overflow: hidden;
    box-shadow: 0 6px 18px rgba(0,0,0,.18);
  }

  /* Contact side */
  .card--contact {
    background: var(--card-white);
    border-bottom: 4px solid var(--brand-blue);
  }
  .contact-logo {
    position: absolute; left: 36px; top: 60px; width: 210px;
    display: flex; flex-direction: column; align-items: center; gap: 12px;
  }
  .contact-logo .mascot-art {
    width: 150px; height: 150px; border-radius: 8px;
    background: linear-gradient(180deg, var(--figure-blue) 0%, var(--figure-blue) 50%, var(--figure-tan) 100%);
  }
  .wordmark {
    font-weight: 700; color: var(--brand-blue); text-transform: uppercase;
    letter-spacing: .5px; line-height: 1.1; text-align: center;
  }
  .contact-logo .wordmark { font-size: 24px; }
  .contact-info {
    position: absolute; left: 280px; top: 62px; right: 20px;
  }
  .contact-name {
    font-size: 25px; font-weight: 500; color: var(--brand-blue);
    text-transform: uppercase; letter-spacing: .5px; margin-bottom: 16px;
  }
  .contact-list { list-style: none; }
  .contact-list li {
    display: flex; align-items: center; gap: 8px;
    font-size: 14.5px; color: var(--ink); margin-bottom: 7px; white-space: nowrap;
  }
  .contact-list svg { width: 14px; height: 14px; flex: none; fill: var(--brand-blue); }
  .license { margin-top: 18px; font-size: 17px; color: var(--brand-blue); }
  .license .license-number { color: var(--brand-yellow); }

  /* Brand side */
  .card--brand {
    background: radial-gradient(ellipse at 40% 40%, var(--water-light) 0%, var(--water-mid) 55%, var(--water-deep) 100%);
  }
  .brand-water {
    position: absolute; inset: 0;
    background: radial-gradient(circle at 30% 30%, rgba(255,255,255,.18), transparent 60%);
  }
  .brand-mascot {
    position: absolute; right: 24px; top: 14px; width: 200px; height: 306px;
    border-radius: 10px 10px 0 0;
    background: linear-gradient(180deg, #5a4030 0%, var(--figure-blue) 30%, var(--figure-blue) 62%, var(--figure-tan) 100%);
  }
  .brand-name {
    position: absolute; left: 40px; bottom: 46px;
    display: flex; align-items: center; gap: 12px;
  }
  .brand-name .wordmark { color: #ffffff; font-size: 36px; text-align: left; }
  .brand-name .brand-dot {
    width: 16px; height: 16px; border-radius: 50%; background: var(--brand-yellow);
  }
</style>
</head>
<body>
<main class="sheet">
  <section class="card card--contact">
    <div class="contact-logo">
      <div class="mascot-art" role="img" aria-label="Cartoon plumber mascot carrying a pipe wrench and a circular saw"></div>
      <div class="wordmark">Bramley<br>Pipeworks</div>
    </div>
    <div class="contact-info">
      <h1 class="contact-name">Rodney Ashcombe</h1>
      <ul class="contact-list">
        <li>
          <svg viewBox="0 0 24 24" aria-hidden="true"><path d="M6.6 10.8a15.1 15.1 0 0 0 6.6 6.6l2.2-2.2a1 1 0 0 1 1-.25 11.4 11.4 0 0 0 3.6.57 1 1 0 0 1 1 1V20a1 1 0 0 1-1 1A17 17 0 0 1 3 4a1 1 0 0 1 1-1h3.5a1 1 0 0 1 1 1c0 1.25.2 2.45.57 3.57a1 1 0 0 1-.25 1z"/></svg>
          (555) 218-7730
        </li>
        <li>
          <svg viewBox="0 0 24 24" aria-hidden="true"><path d="M2 5h20v14H2z M4 7v.3l8 5.2 8-5.2V7z" fill-rule="evenodd"/></svg>
          Info@bramleypipeworks.example
        </li>
        <li>
          <svg viewBox="0 0 24 24" aria-hidden="true"><circle cx="12" cy="12" r="10"/><path d="M2 12h20M12 2c3 3 3 17 0 20M12 2c-3 3-3 17 0 20" stroke="#fff" stroke-width="1.4" fill="none"/></svg>
          www.bramleypipeworks.example
        </li>
      </ul>
      <p class="license">License <span class="license-number"># 4627195</span></p>
    </div>
  </section>

  <section class="card card--brand">
    <div class="brand-water" role="img" aria-label="Close-up of water droplets on a blue surface"></div>
    <div class="brand-mascot" role="img" aria-label="Cartoon plumber mascot holding a pipe wrench and a circular saw"></div>
    <div class="brand-name">
      <span class="brand-dot"></span>
      <span class="wordmark">Bramley<br>Pipeworks</span>
    </div>
  </section>
</main>
</body>
</html>
```